Harbourline Electrical Solutions

On one side. LOGO (underneath:) Commercial Industrial Residential

- NAME & CONTACT DETAILS

Marcus T. Hollings
Project Manager

(Cell icon) (441) 555-0187
(Email icon) hlelectricalsolutions@mailvento.com
(Facebook & Instagram icons )@hlelectricalsolutions

Other side: LOGO - underneath ELECTRICAL CONSTRUCTION & MAINTENANCE . LED LIGHTING & AUTOMATION . LIFE SAFETY SYSTEMS (FIRE ALARM / SECURITY) . DATA & COMMUNICATION

```html
<!DOCTYPE html>
<html lang="en">
<head>
<meta charset="utf-8">
<title>Harbourline Electrical Solutions – Business Cards</title>
<link href="https://fonts.googleapis.com/css2?family=Montserrat:wght@500;600;700&family=Work+Sans:wght@400;500&display=swap" rel="stylesheet">
<style>
  :root {
    --backdrop: #e4e4e4;
    --card-dark: #141414;
    --card-light: #ffffff;
    --teal: #1b5468;
    --grey-text: #5c5c5c;
    --grey-mark: #8a8a8a;
    --white: #ffffff;
    --rule-dark: #6b6b6b;
  }
  * { margin: 0; padding: 0; box-sizing: border-box; }
  html, body { width: 1200px; height: 900px; overflow: hidden; }
  body {
    background: var(--backdrop);
    display: flex;
    flex-direction: column;
    align-items: center;
    justify-content: center;
    gap: 36px;
    font-family: "Work Sans", Arial, sans-serif;
  }
  .card {
    width: 720px;
    height: 400px;
    border-radius: 22px;
    position: relative;
    box-shadow: 0 6px 18px rgba(0,0,0,.18);
  }

  /* ---------- Back (dark) ---------- */
  .card--back { background: var(--card-dark); color: var(--white); }
  .back-brand {
    position: absolute;
    top: 62px; right: 60px;
    display: flex;
    align-items: center;
    gap: 22px;
  }
  .back-brand__mark {
    font-family: "Montserrat", sans-serif;
    font-weight: 700;
    font-size: 40px;
    letter-spacing: 1px;
    color: var(--grey-mark);
  }
  .back-brand__rule { width: 2px; height: 110px; background: var(--rule-dark); }
  .back-brand__name {
    font-family: "Montserrat", sans-serif;
    font-weight: 500;
    font-size: 22px;
    line-height: 1.15;
    letter-spacing: 5px;
    color: #bdbdbd;
    text-transform: uppercase;
  }
  .services {
    position: absolute;
    left: 70px; top: 220px;
    list-style: none;
    font-family: "Montserrat", sans-serif;
    font-weight: 600;
    font-size: 17px;
    letter-spacing: 1.5px;
    line-height: 1.42;
    text-transform: uppercase;
  }
  .services li { position: relative; padding-left: 24px; }
  .services li::before {
    content: "";
    position: absolute;
    left: 0; top: 8px;
    width: 7px; height: 7px;
    border-radius: 50%;
    background: var(--white);
  }

  /* ---------- Front (light) ---------- */
  .card--front { background: var(--card-light); }
  .front-brand {
    position: absolute;
    left: 60px; top: 130px;
    font-family: "Montserrat", sans-serif;
    font-weight: 700;
    font-size: 36px;
    color: var(--teal);
    letter-spacing: .5px;
  }
  .front-rule {
    position: absolute;
    left: 330px; top: 110px;
    width: 2px; height: 120px;
    background: var(--grey-mark);
  }
  .contact {
    position: absolute;
    left: 360px; top: 112px;
  }
  .contact__name {
    font-family: "Montserrat", sans-serif;
    font-weight: 700;
    font-size: 24px;
    letter-spacing: 1px;
    color: var(--teal);
    text-transform: uppercase;
  }
  .contact__role {
    font-size: 18px;
    color: var(--grey-text);
    margin-bottom: 10px;
  }
  .contact__line {
    display: flex;
    align-items: center;
    gap: 10px;
    font-size: 18px;
    color: var(--grey-text);
    line-height: 1.55;
  }
  .contact__line svg { width: 16px; height: 16px; flex: none; }
  .social {
    position: absolute;
    left: 200px; bottom: 58px;
    display: flex;
    align-items: center;
    gap: 10px;
    font-size: 19px;
    color: var(--grey-text);
  }
  .social__square { width: 20px; height: 20px; background: var(--teal); border-radius: 3px; }
</style>
</head>
<body>

  <section class="card card--back">
    <div class="back-brand">
      <span class="back-brand__mark">Harbourline</span>
      <span class="back-brand__rule"></span>
      <span class="back-brand__name">Harbourline<br>Electrical<br>Solutions</span>
    </div>
    <ul class="services">
      <li>Data &amp; Communication</li>
      <li>LED Lighting &amp; Automation</li>
      <li>Electrical Construction &amp; Maintenance</li>
      <li>Life Safety Systems (Fire Alarm / Security)</li>
    </ul>
  </section>

  <section class="card card--front">
    <div class="front-brand">Harbourline</div>
    <span class="front-rule"></span>
    <div class="contact">
      <p class="contact__name">Marcus T. Hollings</p>
      <p class="contact__role">Project Manager</p>
      <p class="contact__line">
        <svg viewBox="0 0 16 16" aria-hidden="true"><path d="M4 1.5c.6 0 1.9 2.6 1.9 3.2 0 .6-1.3 1.1-1.3 1.8 0 1.3 2.6 4.3 3.9 4.3.6 0 1.1-1.3 1.8-1.3.6 0 3.2 1.3 3.2 1.9C13.5 13 12 14.5 11 14.5 6.5 14.5 1.5 9.5 1.5 5 1.5 4 3 1.5 4 1.5z" fill="var(--teal)"/></svg>
        (441) 555-0187
      </p>
      <p class="contact__line">
        <svg viewBox="0 0 16 16" aria-hidden="true"><rect x="1.5" y="3.5" width="13" height="9" rx="1" fill="none" stroke="var(--teal)" stroke-width="1.4"/><path d="M2 4l6 5 6-5" fill="none" stroke="var(--teal)" stroke-width="1.4"/></svg>
        hlelectricalsolutions@mailvento.com
      </p>
    </div>
    <div class="social">
      <span class="social__square"></span>
      @hlelectricalsolutions
    </div>
  </section>

</body>
</html>
```